Detail Shop Business card design

i need a business card design for my new detailing company called 'Brisk's Polish Works'. i want an all black and white design . simple, direct and to the point. i want the designer to choose a fitting font to match the logothe front should have logo, address, phone and email and the back side should have a slogan and text indicating that we offer services on anything including cars, trucks, motorcycles and RVs. slogan will read "we take pride in your ride"
maybe also very small on the back side the IG icon with Brisks_Polish_Works

phone 208.417.6352
address 3847 E Larkin Ave
Spokane WA 99214
email: BrisksPolish@mailvexo.com

Target Market(s)

all ages , auto enthusiasts

Industry/Entity Type

Automotive

Contact Information for Business Card

the front should have logo, address, phone and email and the back side should have a slogan and text indicating that we offer services on anything including cars, trucks, motorcycles and RVs. slogan will read "we take pride in your ride"

phone 208.417.6352
address 3847 E Larkin Ave
Spokane WA 99214

Colors
000000
ffffff

Requirements
Must have
• bold font and very simple design with good spacing
Nice to have
• anything creative from the designer indicating we service any types of vehicles
Should not have
• any colors ,

```html
<!DOCTYPE html>
<html lang="en">
<head>
<meta charset="utf-8">
<title>Brisk's Polish Works – Business Card</title>
<link rel="stylesheet" href="https://fonts.googleapis.com/css2?family=Open+Sans:wght@400;600;700;800&display=swap">
<style>
  :root {
    --backdrop: #2a2624;
    --card: #0c0c0c;
    --gloss: #4a4a4a;
    --gloss-bright: #6a6a6a;
    --ink: #ffffff;
    --ink-soft: #d8d8d8;
    --art-dark: #cfcfcf;
    --art-light: #ffffff;
  }
  * { box-sizing: border-box; margin: 0; padding: 0; }
  html, body { width: 1200px; height: 864px; overflow: hidden; }
  body {
    background: var(--backdrop);
    font-family: "Open Sans", Arial, sans-serif;
    display: flex;
    align-items: center;
    justify-content: center;
    gap: 40px;
  }
  .card {
    width: 560px;
    height: 320px;
    background: var(--card);
    border-radius: 4px;
    position: relative;
    overflow: hidden;
  }

  /* Back side */
  .card--back {
    display: flex;
    flex-direction: column;
    align-items: center;
    justify-content: center;
    text-align: center;
  }
  .brand {
    display: flex;
    align-items: center;
    gap: 12px;
    color: var(--gloss-bright);
    font-weight: 800;
    font-size: 30px;
    letter-spacing: 0.5px;
    margin-bottom: 34px;
  }
  .brand__dot {
    width: 20px; height: 20px;
    border-radius: 50%;
    background: var(--gloss-bright);
  }
  .slogan {
    color: var(--gloss-bright);
    font-weight: 800;
    font-size: 19px;
    letter-spacing: 0.6px;
    text-transform: uppercase;
  }
  .slogan-rule {
    width: 340px;
    height: 2px;
    background: var(--gloss);
    margin: 10px 0;
  }
  .services {
    color: var(--gloss-bright);
    font-weight: 600;
    font-size: 13.5px;
  }

  /* Front side */
  .card--front {
    display: flex;
    align-items: center;
    padding: 0 0 0 40px;
  }
  .vehicle-art {
    width: 220px;
    height: 120px;
    border-radius: 60px 60px 6px 6px;
    background: linear-gradient(180deg, var(--art-light), var(--art-dark));
    flex: none;
  }
  .divider {
    width: 1.5px;
    height: 190px;
    background: var(--ink-soft);
    margin: 0 26px 0 36px;
    flex: none;
  }
  .contact { color: var(--ink); }
  .contact__name {
    font-weight: 700;
    font-size: 22px;
    text-transform: uppercase;
    line-height: 1.1;
  }
  .contact__role {
    font-size: 14px;
    text-transform: uppercase;
    margin-bottom: 12px;
  }
  .contact__address { font-size: 15px; line-height: 1.3; margin-bottom: 6px; }
  .contact__list { list-style: none; font-size: 15px; line-height: 1.45; }
  .contact__list li { display: flex; align-items: center; gap: 8px; }
  .contact__list svg { width: 13px; height: 13px; fill: var(--ink); flex: none; }
</style>
</head>
<body>

  <section class="card card--back" aria-label="Card back">
    <div class="brand"><span class="brand__dot"></span>Brisk's Polish Works</div>
    <p class="slogan">We take pride in your ride</p>
    <div class="slogan-rule"></div>
    <p class="services">we offer services on anything including cars, trucks, motorcycles &amp; RVs</p>
  </section>

  <section class="card card--front" aria-label="Card front">
    <div class="vehicle-art" role="img" aria-label="White illustration of a classic hot rod car"></div>
    <div class="divider"></div>
    <div class="contact">
      <p class="contact__name">Mara Lindqvist</p>
      <p class="contact__role">President</p>
      <p class="contact__address">3847 E Larkin Ave<br>Spokane WA 99214</p>
      <ul class="contact__list">
        <li><svg viewBox="0 0 16 16"><path d="M3 1h3l1.5 4-2 1.5a9 9 0 0 0 4 4L11 8.5l4 1.5v3a2 2 0 0 1-2 2A12 12 0 0 1 1 3a2 2 0 0 1 2-2z"/></svg>208.417.6352</li>
        <li><svg viewBox="0 0 16 16"><path d="M4 0h8a1 1 0 0 1 1 1v14a1 1 0 0 1-1 1H4a1 1 0 0 1-1-1V1a1 1 0 0 1 1-1zm1 2v10h6V2z"/></svg>208 552 7190</li>
        <li><svg viewBox="0 0 16 16"><path d="M1 3h14v10H1zm1 1.5v.3l6 4 6-4v-.3z"/></svg>BrisksPolish@mailvexo.com</li>
        <li><svg viewBox="0 0 16 16"><path d="M8 0a8 8 0 1 0 0 16A8 8 0 0 0 8 0zm0 2c1 1 1.6 3 1.7 5H6.3C6.4 5 7 3 8 2zM2.1 9h2.2c.1 1.8.5 3.2 1.1 4.3A6 6 0 0 1 2.1 9zm0-2a6 6 0 0 1 3.3-4.3C4.8 3.8 4.4 5.2 4.3 7zm4.2 2h3.4c-.1 2-.7 4-1.7 5-1-1-1.6-3-1.7-5zm5.4 0h2.2a6 6 0 0 1-3.3 4.3c.6-1.1 1-2.5 1.1-4.3zm0-2c-.1-1.8-.5-3.2-1.1-4.3A6 6 0 0 1 13.9 7z"/></svg>www.briskspolishworks.com</li>
      </ul>
    </div>
  </section>

</body>
</html>
```